Small environmental consultancy needs a simple but professional web design

We are a boutique environmental consultancyand contracting business located in Margaret River in the South West of Western Australia.

We have two arms
1) Consulting which offers environmental planning, management and assessment services primarily to local government and the development industry.
2) Contracting which implements on site plans and on ground works primarily involving revegetation, bush regeneration and environmental weed control.

We need a simple yet professional web design within the wordpress platform that commmunicates professionalism, experience and technical expertise without appearing too corporate.

Something like this structure appeals:
http://fernquill.net.au/environment-services/
or
http://www.tallowbrookenvironmental.com.au/index.php

(without the image gallery function)

Target Market(s)

Local Government Officers deciding on tenders;
Developers, Engineers, Town Planning consultants looking for environmental expertise

Industry/Entity Type

Business

Number of Pages Required

5+ page

Font styles to use
Sans Serif

Colors
33a6d7
9bcb3c

Requirements
Must have
• Pages required include:
• Home
• Environmental Planning and Management
• Revegetation and Regeneration Implementation (This page can mirror the Environmental Planning and Management page exactly in structure but with different text and images)
• About Us (I think that this page can be relatively simple and generic)
• Contact (I think that this page can be very simple and generic)
Nice to have
• An ability to start out basic and quicikly establish a website presence and then build in additional drop downs and pages over time.
Should not have
• It does not need a photo gallery page;
• It does not need a major amount of space dedicated to social media and blogs etc as this is not currently particularly active area for us

```html
<!DOCTYPE html>
<html lang="en">
<head>
<meta charset="utf-8">
<title>Banksia Ecoservices</title>
<link href="https://fonts.googleapis.com/css2?family=Open+Sans:wght@300;400;600;700&display=swap" rel="stylesheet">
<style>
:root{
  --green:#7fab23;
  --green-light:#9bcb3c;
  --blue:#33a6d7;
  --ink:#333333;
  --body:#555555;
  --muted:#8a8a8a;
  --line:#dddddd;
  --band:#e9e9e9;
  --footer:#ececec;
  --white:#ffffff;
}
*{box-sizing:border-box;margin:0;padding:0}
html,body{width:1200px;height:2257px;overflow:hidden;background:var(--white)}
body{position:relative;font-family:"Open Sans",Arial,sans-serif;color:var(--ink)}
.abs{position:absolute}

/* Header */
.site-header{left:0;top:0;width:1200px;height:107px;background:linear-gradient(90deg,#fafaf7 0%,#ffffff 40%,#f2f6fa 100%)}
.brand{left:88px;top:28px;display:flex;align-items:center;gap:10px}
.brand-mark{width:26px;height:26px;border-radius:50%;background:var(--green-light)}
.brand-name{font-size:19px;font-weight:600;color:var(--green)}
.brand-tag{left:90px;top:66px;font-size:8px;color:var(--muted)}
.search{left:875px;top:10px;width:169px;height:20px;border-bottom:1px solid #999;font-size:11px;color:var(--muted);padding-left:4px;line-height:18px}
.search svg{position:absolute;right:2px;top:3px}
.main-nav{left:300px;top:75px;display:flex;gap:22px;font-size:11.5px;font-weight:600;color:var(--ink);letter-spacing:.1px}

/* Hero */
.hero{left:0;top:107px;width:1200px;height:478px;background:linear-gradient(180deg,#3a8fd6 0%,#7fb9e6 35%,#5d8a3a 62%,#6fae2e 85%,#4f8a22 100%)}
.hero-blossom{left:0;top:107px;width:560px;height:478px;background:radial-gradient(ellipse at 35% 40%,#e8d6dc 0%,#cdb8bf 40%,rgba(120,110,90,0) 75%)}
.hero-title{left:513px;top:140px;color:var(--white);font-size:41px;line-height:46px;font-weight:600}
.hero-title span{display:block;font-weight:300}
.hero-dots{left:164px;top:552px;display:flex;gap:6px}
.hero-dots i{width:15px;height:15px;border-radius:50%;background:rgba(255,255,255,.75);display:block}
.hero-dots i.active{background:var(--green-light)}

/* Welcome */
.section-title{font-size:24px;font-weight:700;color:var(--ink)}
.section-title span{font-weight:400}
.welcome-title{left:160px;top:606px}
.welcome-text{left:160px;top:645px;width:880px;font-size:11.4px;line-height:16.5px;color:var(--body)}

/* Services */
.services-title{left:160px;top:732px}
.services-grid{left:160px;top:779px;width:879px;height:240px;display:grid;grid-template-columns:repeat(6,146.5px);grid-template-rows:repeat(2,120px);border-top:1px solid var(--line);border-bottom:1px solid var(--line)}
.service-photo{width:100%;height:100%}
.service-card{position:relative;background:var(--white);padding:12px 10px 0 14px;font-size:11px;line-height:15px;color:var(--body)}
.service-card h3{font-size:10.5px;font-weight:600;color:var(--ink);margin-bottom:9px}
.service-card b{color:var(--ink)}
.service-card::before{content:"";position:absolute;left:-10px;top:20px;border:10px solid transparent;border-left:0;border-right-color:var(--white)}
.service-card.point-right::before{left:auto;right:-10px;border-right:0;border-left:10px solid var(--white);border-top-color:transparent;border-bottom-color:transparent}
.photo-1{background:linear-gradient(135deg,#8c9a7a,#5c6b4a)}
.photo-2{background:radial-gradient(circle at 50% 50%,#c9432a 0,#7ea04a 60%)}
.photo-3{background:radial-gradient(circle at 50% 55%,#c8c22a 0,#5a3b4a 60%)}
.photo-4{background:radial-gradient(circle at 50% 50%,#c0409a 0,#6c9a3a 65%)}
.photo-5{background:radial-gradient(circle at 50% 50%,#e0832a 0,#6a4a2a 70%)}
.photo-6{background:radial-gradient(circle at 50% 50%,#6a4ab0 0,#8aa24a 70%)}

/* Projects */
.projects-title{left:173px;top:1055px;font-size:32px;line-height:38px;font-weight:700;color:var(--ink)}
.projects-title span{display:block;font-weight:400}
.projects-text{left:173px;top:1150px;width:400px;font-size:12.3px;line-height:17.6px;color:var(--muted)}
.projects-photo{left:600px;top:1065px;width:427px;height:197px;background:radial-gradient(circle at 50% 45%,#d8f29a 0%,#7fc23a 45%,#3d7a1f 100%)}

/* Why us */
.why-band{left:0;top:1294px;width:1200px;height:282px;background:var(--band)}
.why-title{left:173px;top:1322px;font-size:22px}
.why-item{top:1386px;width:150px}
.why-circle{width:120px;height:120px;border-radius:50%;background:var(--white);display:flex;align-items:center;justify-content:center}
.why-icon{width:60px;height:60px;border-radius:50%;background:var(--blue)}
.why-label{margin-top:20px;font-size:12.5px;line-height:14px;color:var(--body);text-transform:uppercase}

/* Testimonials */
.testimonials-title{left:0;top:1609px;width:1200px;text-align:center;font-size:24px;font-weight:700}
.title-rule{left:585px;top:1655px;width:30px;height:3px;background:var(--green)}
.quote{top:1696px;width:240px}
.quote-mark{position:absolute;left:0;top:0;font-size:48px;line-height:40px;font-weight:700;color:var(--green-light);font-family:Georgia,serif}
.quote-text{margin-left:32px;width:172px;font-size:10.6px;line-height:17px;color:var(--body);height:85px;overflow:hidden}
.quote-author{margin:10px 0 0 32px;font-size:11px;font-weight:600;color:var(--ink)}
.avatar{width:102px;height:102px;border-radius:50%;border:3px solid #9a9a9a;background:linear-gradient(180deg,#d8d8d8,#b9b9b9)}
.arrow{top:1785px}

/* Footer */
.site-footer{left:0;top:1990px;width:1200px;height:267px;background:var(--footer)}
.footer-heading{font-size:13.5px;font-weight:400;color:var(--ink);text-transform:uppercase}
.footer-links{margin-top:8px;font-size:11px;line-height:16px;color:var(--ink);list-style:none}
.about-col{left:171px;top:2018px}
.legal-col{left:427px;top:2018px}
.call-col{left:171px;top:2118px}
.phone{margin-top:8px;display:flex;align-items:center;gap:8px;font-size:18px;color:var(--green)}
.contact-col{left:611px;top:2022px}
.field{position:absolute;height:27px;background:var(--white);border:1px solid var(--line);font-size:13px;color:#aaa;padding:4px 8px}
.field svg{position:absolute;right:6px;top:6px}
.send-btn{left:611px;top:2158px;width:127px;height:33px;background:var(--green);color:var(--white);font-size:14px;line-height:33px;text-align:center;border-bottom:2px solid #5d8418}
.footer-rule{left:171px;top:2220px;width:858px;height:1px;background:var(--line)}
.copyright{left:171px;top:2229px;font-size:10.5px;color:var(--body)}
</style>
</head>
<body>

<header class="abs site-header">
  <div class="abs brand"><span class="brand-mark"></span><span class="brand-name">Banksia Ecoservices</span></div>
  <div class="abs brand-tag">Environmental Assessment, Planning &amp; Management</div>
  <div class="abs search">Search
    <svg width="14" height="14" viewBox="0 0 14 14"><circle cx="6" cy="6" r="4.5" fill="none" stroke="#777" stroke-width="1.5"/><line x1="9.3" y1="9.3" x2="13" y2="13" stroke="#777" stroke-width="1.6"/></svg>
  </div>
  <nav class="abs main-nav">
    <span>HOME</span><span>ENVIRONMENTAL PLANNING AND MANAGEMENT</span><span>REVEGETATION AND BUSH REGENERATION</span><span>ABOUT US</span><span>CONTACTS</span>
  </nav>
</header>

<section>
  <div class="abs hero" role="img" aria-label="Spring parkland with a flowering blossom tree, green lawn and woodland under blue sky"></div>
  <div class="abs hero-blossom"></div>
  <h1 class="abs hero-title">Lorem Ipsum Dolor Sit Amet<span>Consectetur Adipiscing Elit.</span></h1>
  <div class="abs hero-dots"><i class="active"></i><i></i><i></i><i></i><i></i></div>
</section>

<section>
  <h2 class="abs section-title welcome-title">Welcome to <span>Banksia Ecoservices</span></h2>
  <p class="abs welcome-text">Lorem ipsum dolor sit amet, consectetur adipiscing elit, sed do eiusmod tempor incididunt ut labore et dolore magna aliqua. Ut enim ad minim veniam, quis nostrud exercitation ullamco laboris nisi ut aliquip ex ea commodo consequat. Duis aute irure dolor in reprehenderit in voluptate velit esse cillum dolore eu fugiat nulla pariatur. Excepteur sint occaecat cupidatat non proident, sunt in culpa qui officia deserunt mollit anim id est laborum. Lorem ipsum dolor sit amet, consectetur adipiscing elit, sed do eiusmod tempor incididunt ut labore et dolore magna aliqua.</p>
</section>

<section>
  <h2 class="abs section-title services-title">Our <span>Services</span></h2>
  <div class="abs services-grid">
    <div class="service-photo photo-1" role="img" aria-label="Gnarled eucalypt trunk in bushland"></div>
    <div class="service-card"><h3>NAME OF SERVICE</h3>Sed ut perspiciatis unde omnis iste natus error accusantium doloremque <b>[...]</b></div>
    <div class="service-photo photo-2" role="img" aria-label="Red native wildflower among leaves"></div>
    <div class="service-card"><h3>NAME OF SERVICE</h3>Sed ut perspiciatis unde omnis iste natus error accusantium doloremque <b>[...]</b></div>
    <div class="service-photo photo-3" role="img" aria-label="Yellow and purple native orchid"></div>
    <div class="service-card"><h3>NAME OF SERVICE</h3>Sed ut perspiciatis unde omnis iste natus error accusantium doloremque <b>[...]</b></div>

    <div class="service-card point-right"><h3>NAME OF SERVICE</h3>Sed ut perspiciatis unde omnis iste natus error accusantium doloremque <b>[...]</b></div>
    <div class="service-photo photo-4" role="img" aria-label="Purple thistle flower"></div>
    <div class="service-card point-right"><h3>NAME OF SERVICE</h3>Sed ut perspiciatis unde omnis iste natus error accusantium doloremque <b>[...]</b></div>
    <div class="service-photo photo-5" role="img" aria-label="Orange and red pea flowers"></div>
    <div class="service-card point-right"><h3>NAME OF SERVICE</h3>Sed ut perspiciatis unde omnis iste natus error accusantium doloremque <b>[...]</b></div>
    <div class="service-photo photo-6" role="img" aria-label="Violet native flowers on green stems"></div>
  </div>
</section>

<section>
  <h2 class="abs projects-title">Recent Projects<span>Lorem ipsum dolor sit</span></h2>
  <p class="abs projects-text">Sed ut perspiciatis unde omnis iste natus error sit voluptatem accusantium doloremque laudantium, totam rem aperiam, eaque ipsa quae ab illo inventore veritatis et quasi architecto beatae vitae dicta sunt explicabo. Nemo enim ipsam voluptatem quia voluptas sit aspernatur aut odit aut fugit, sed quia consequuntur magni dolores eos qui ratione voluptatem sequi nesciunt.</p>
  <div class="abs projects-photo" role="img" aria-label="Looking up into a sunlit green forest canopy"></div>
</section>

<section>
  <div class="abs why-band"></div>
  <h2 class="abs section-title why-title">Why <span>Us?</span></h2>
  <div class="abs why-item" style="left:162px"><div class="why-circle"><div class="why-icon" role="img" aria-label="Feature icon"></div></div><p class="why-label">Lorem ipsum<br>dolor sit</p></div>
  <div class="abs why-item" style="left:310px"><div class="why-circle"><div class="why-icon" role="img" aria-label="Feature icon"></div></div><p class="why-label">Lorem ipsum<br>dolor sit</p></div>
  <div class="abs why-item" style="left:459px"><div class="why-circle"><div class="why-icon" role="img" aria-label="Feature icon"></div></div><p class="why-label">Lorem ipsum<br>dolor sit</p></div>
  <div class="abs why-item" style="left:606px"><div class="why-circle"><div class="why-icon" role="img" aria-label="Feature icon"></div></div><p class="why-label">Lorem ipsum<br>dolor sit</p></div>
  <div class="abs why-item" style="left:754px"><div class="why-circle"><div class="why-icon" role="img" aria-label="Feature icon"></div></div><p class="why-label">Lorem ipsum<br>dolor sit</p></div>
  <div class="abs why-item" style="left:903px"><div class="why-circle"><div class="why-icon" role="img" aria-label="Feature icon"></div></div><p class="why-label">Lorem ipsum<br>dolor sit</p></div>
</section>

<section>
  <h2 class="abs testimonials-title">Testimonials</h2>
  <div class="abs title-rule"></div>
  <svg class="abs arrow" style="left:172px" width="20" height="40" viewBox="0 0 20 40"><polyline points="18,2 2,20 18,38" fill="none" stroke="#c8c8c8" stroke-width="2"/></svg>
  <svg class="abs arrow" style="left:1008px" width="20" height="40" viewBox="0 0 20 40"><polyline points="2,2 18,20 2,38" fill="none" stroke="#c8c8c8" stroke-width="2"/></svg>

  <div class="abs quote" style="left:222px"><span class="quote-mark">&ldquo;</span>
    <p class="quote-text">Thank you for seeing my husband, Ewan. He could not believe the difference in patient care that he experienced with you and Dr. Marsh. Thanks for</p>
    <p class="quote-author">- Ruth Calloway</p></div>
  <div class="abs quote" style="left:498px"><span class="quote-mark">&ldquo;</span>
    <p class="quote-text">He and his staff at Cove Street Dental care for and take an interest in every patient, but what really sets them apart is that Dr. Kellet is really a very fine</p>
    <p class="quote-author">- Dr. Ben Harlow</p></div>
  <div class="abs quote" style="left:773px"><span class="quote-mark">&ldquo;</span>
    <p class="quote-text">My daughter's friend admired her teeth, saying, "They're so beautiful. Just like your mother's." My daughter replied, "Thank you. But my mother's have only been</p>
    <p class="quote-author">- Judy Penrose</p></div>

  <div class="abs avatar" style="left:244px;top:1832px" role="img" aria-label="Portrait of client"></div>
  <div class="abs avatar" style="left:519px;top:1832px" role="img" aria-label="Portrait of client"></div>
  <div class="abs avatar" style="left:795px;top:1832px" role="img" aria-label="Portrait of client"></div>
</section>

<footer>
  <div class="abs site-footer"></div>
  <div class="abs about-col"><h4 class="footer-heading">About</h4>
    <ul class="footer-links"><li>Environmental Planning and Management</li><li>Revegetation and Bush Regeneration</li><li>Contacts</li></ul></div>
  <div class="abs legal-col"><h4 class="footer-heading">Legal</h4>
    <ul class="footer-links"><li>Terms of Service</li><li>Privacy Policy</li><li>Cookie Policy</li></ul></div>
  <div class="abs call-col"><h4 class="footer-heading">Call us now:</h4>
    <p class="phone"><svg width="16" height="16" viewBox="0 0 16 16"><path d="M3 1l3 3-1.5 2a9 9 0 0 0 5.5 5.5L12 10l3 3-2 2C7 15 1 9 1 3z" fill="#555"/></svg>+61 8 9555 0142</p></div>
  <div class="abs contact-col"><h4 class="footer-heading">Contact us</h4></div>
  <div class="field" style="left:611px;top:2054px;width:203px">Name
    <svg width="14" height="14" viewBox="0 0 14 14"><circle cx="7" cy="4" r="3" fill="#aaa"/><path d="M1 14c0-4 3-6 6-6s6 2 6 6z" fill="#aaa"/></svg></div>
  <div class="field" style="left:822px;top:2054px;width:199px">E-mail
    <svg width="16" height="12" viewBox="0 0 16 12"><rect width="16" height="12" fill="#aaa"/><polyline points="0,0 8,7 16,0" fill="none" stroke="#fff" stroke-width="1.4"/></svg></div>
  <div class="field" style="left:611px;top:2092px;width:410px;height:56px">Message
    <svg width="14" height="12" viewBox="0 0 14 12"><path d="M0 0h14v9H5l-3 3V9H0z" fill="#aaa"/></svg></div>
  <div class="abs send-btn">Send Message</div>
  <div class="abs footer-rule"></div>
  <p class="abs copyright">&copy; 2015, Banksia Ecoservices. All Rights Reserved.</p>
</footer>

</body>
</html>
```